American cannabis tech company business card design

Pavrel.com is seeking a modern, professional, and brand-aligned business card that represents our company and its core values: Mission, Story, Values, and Impact. As an innovative cannabis company, we want a business card that is not only visually appealing but also serves as a representation of who we are and what we stand for.

Project Scope: Design a double-sided business card that integrates our brand identity and core values. Incorporate our key brand elements, ensuring a sleek and contemporary aesthetic. Visually reflect our core values (Mission, Story, Values, Impact) in a way that is engaging yet professional.

Target Market(s)

Vendors, third parties,

Contact Information for Business Card

Contact details (name, title, email, phone, website, etc.)

Font styles to use
Other font styles liked:
• Caslon, Centra

Colors

Designer to choose colors to be used in the design.

Requirements
Must have
• Pavrel.com logo and branding A creative yet clean way to integrate our core values (Mission, Story, Values, Impact) Modern typography and a well-structured layout
Nice to have
• forest green, grey, white, black
Should not have
• references to marijuana, leafs, plants, or related product

```html
<!DOCTYPE html>
<html lang="en">
<head>
<meta charset="utf-8">
<title>Pavrel.com Business Card</title>
<link href="https://fonts.googleapis.com/css2?family=Montserrat:wght@400;500;600&family=Playfair+Display:wght@700;900&display=swap" rel="stylesheet">
<style>
  :root {
    --forest: #1b3419;
    --forest-deep: #14280f;
    --forest-light: #23502a;
    --paper: #ffffff;
    --paper-muted: rgba(255,255,255,0.72);
    --ink: #111a10;
    --backdrop: #cfd4d4;
  }
  * { margin: 0; padding: 0; box-sizing: border-box; }
  html, body { width: 1200px; height: 1050px; overflow: hidden; }
  body { background: var(--backdrop); position: relative; }

  .card {
    position: absolute;
    left: 290px;
    width: 620px;
    height: 354px;
    border-radius: 4px;
    overflow: hidden;
    box-shadow: 0 18px 40px rgba(0,0,0,0.18);
  }
  .card-front { top: 120px; background: var(--paper); }
  .card-back { top: 566px; background: var(--forest); }

  .front-wave { position: absolute; inset: 0; }

  .wordmark {
    position: absolute;
    top: 46px;
    left: 0;
    right: 0;
    text-align: center;
    font-family: "Playfair Display", Georgia, serif;
    font-weight: 900;
    font-size: 104px;
    letter-spacing: 1px;
    color: var(--forest);
    line-height: 1;
  }

  .identity {
    position: absolute;
    top: 198px;
    right: 330px;
    text-align: right;
    font-family: "Playfair Display", Georgia, serif;
    color: var(--forest);
  }
  .identity-name { font-weight: 700; font-size: 19px; line-height: 1.2; }
  .identity-title { font-weight: 700; font-size: 11px; color: var(--ink); margin-top: 3px; }

  .divider {
    position: absolute;
    top: 196px;
    left: 300px;
    width: 1.5px;
    height: 50px;
    background: var(--ink);
  }

  .contact-list {
    position: absolute;
    top: 194px;
    left: 312px;
    list-style: none;
    font-family: "Montserrat", Arial, sans-serif;
    font-size: 12.5px;
    color: var(--ink);
  }
  .contact-list li { display: flex; align-items: center; gap: 7px; height: 20px; }
  .contact-list svg { width: 11px; height: 11px; flex: none; }
  .icon-solid { fill: var(--forest); }
  .icon-line { fill: none; stroke: var(--forest); stroke-width: 2.4; }

  .back-field {
    position: absolute;
    inset: 0;
    background: linear-gradient(155deg, var(--forest-light) 0%, var(--forest) 40%, var(--forest-deep) 100%);
  }
  .back-wordmark {
    position: absolute;
    left: 0;
    right: 0;
    top: 244px;
    text-align: center;
    font-family: "Playfair Display", Georgia, serif;
    font-weight: 900;
    font-size: 30px;
    line-height: 1;
    letter-spacing: 1px;
    color: var(--paper);
  }
  .core-values {
    position: absolute;
    left: 0;
    right: 0;
    top: 286px;
    display: flex;
    justify-content: center;
    gap: 14px;
    list-style: none;
    font-family: "Montserrat", Arial, sans-serif;
    font-weight: 500;
    font-size: 10px;
    letter-spacing: 2.5px;
    text-transform: uppercase;
    color: var(--paper-muted);
  }
  .core-values li + li::before {
    content: "";
    display: inline-block;
    width: 3px;
    height: 3px;
    border-radius: 50%;
    background: var(--paper-muted);
    margin-right: 14px;
    vertical-align: middle;
  }
</style>
</head>
<body>

  <section class="card card-front">
    <svg class="front-wave" viewBox="0 0 620 354" preserveAspectRatio="none" aria-hidden="true">
      <path d="M0,178 C110,178 190,238 290,298 C370,344 520,336 620,300 L620,354 L0,354 Z" fill="var(--forest)"/>
      <path d="M0,205 C110,205 195,262 292,318 C372,360 520,352 620,318" fill="none" stroke="var(--paper)" stroke-width="2.5"/>
    </svg>

    <div class="wordmark">PAVREL</div>

    <div class="identity">
      <div class="identity-name">Daniel Reyes</div>
      <div class="identity-title">Owner</div>
    </div>

    <div class="divider"></div>

    <ul class="contact-list">
      <li>
        <svg viewBox="0 0 24 24" aria-hidden="true"><path class="icon-solid" d="M6.6 10.8a15.1 15.1 0 0 0 6.6 6.6l2.2-2.2a1 1 0 0 1 1-.25 11.4 11.4 0 0 0 3.6.57 1 1 0 0 1 1 1V20a1 1 0 0 1-1 1A17 17 0 0 1 3 4a1 1 0 0 1 1-1h3.5a1 1 0 0 1 1 1c0 1.25.2 2.45.57 3.57a1 1 0 0 1-.25 1z"/></svg>
        555-014-2280
      </li>
      <li>
        <svg viewBox="0 0 24 24" aria-hidden="true"><rect class="icon-line" x="2.5" y="5.5" width="19" height="13" rx="1"/><path class="icon-line" d="M2.5 6l9.5 7 9.5-7"/></svg>
        info@pavrel.com
      </li>
      <li>
        <svg viewBox="0 0 24 24" aria-hidden="true"><circle class="icon-line" cx="12" cy="12" r="9.5"/><path class="icon-line" d="M2.5 12h19M12 2.5c3 3 3 16 0 19M12 2.5c-3 3-3 16 0 19"/></svg>
        www.pavrel.com
      </li>
    </ul>
  </section>

  <section class="card card-back">
    <div class="back-field" role="img" aria-label="Repeating brand name pattern in shades of forest green"></div>
    <div class="back-wordmark">PAVREL</div>
    <ul class="core-values" aria-label="Core values">
      <li>Mission</li>
      <li>Story</li>
      <li>Values</li>
      <li>Impact</li>
    </ul>
  </section>

</body>
</html>
```